Redesign of business card for Cedar Ridge Mechanical

We are looking for a new design for our business cards for Cedar Ridge Mechanical. We are a plumbing & HVAC construction company, operating on the West Coast of Canada and USA. Logo attached.
Industry/Entity Type
Construction - Plumbing & HVAC
Contact Information for Business Card
Name, address, phone numbers, email, website address
Look and feel
Each slider illustrates characteristics of the customer's brand and the style your logo design should communicate.

```html
<!DOCTYPE html>
<html lang="en">
<head>
<meta charset="utf-8">
<title>Cedar Ridge Mechanical – Business Card</title>
<link href="https://fonts.googleapis.com/css2?family=Montserrat:wght@400;500;700&display=swap" rel="stylesheet">
<style>
  :root {
    --stage: #1d1d1f;
    --card-white: #ffffff;
    --card-black: #141414;
    --ink: #1a1a1a;
    --silver: #a9a9a9;
    --silver-light: #d4d4d4;
    --text-light: #f2f2f2;
    --text-muted: #cfcfcf;
  }
  * { margin: 0; padding: 0; box-sizing: border-box; }
  html, body {
    width: 1200px; height: 801px; overflow: hidden;
    background: var(--stage);
    font-family: "Montserrat", sans-serif;
  }
  .stage {
    width: 1200px; height: 801px;
    display: flex; align-items: center; justify-content: center; gap: 40px;
  }
  .card {
    position: relative;
    width: 540px; height: 309px;
    border-radius: 18px;
    overflow: hidden;
    box-shadow: 0 14px 30px rgba(0,0,0,0.55);
  }
  .card-front { background: var(--card-white); }
  .front-shapes { position: absolute; inset: 0; }

  .brand {
    position: absolute;
    display: flex; align-items: center; gap: 10px;
    font-weight: 700; letter-spacing: 0.5px;
  }
  .brand-mark { width: 14px; height: 14px; flex: none; }
  .front-brand { left: 30px; top: 104px; color: var(--ink); font-size: 17px; width: 200px; line-height: 1.25; }
  .front-brand .brand-mark { background: var(--ink); }

  .holder {
    position: absolute; right: 30px; top: 54px; text-align: right; color: var(--text-light);
  }
  .holder-name { font-weight: 700; font-size: 20px; letter-spacing: 1px; }
  .holder-role { font-size: 12px; color: var(--text-muted); margin-top: 2px; }

  .contact-list {
    position: absolute; right: 30px; top: 128px; list-style: none; color: var(--text-light);
    font-size: 12.5px; line-height: 22px; text-align: right;
  }
  .contact-list li { display: flex; align-items: center; justify-content: flex-end; gap: 8px; }
  .contact-icon {
    width: 14px; height: 14px; border-radius: 50%; background: var(--text-light);
    display: inline-flex; align-items: center; justify-content: center;
  }
  .address {
    position: absolute; left: 30px; bottom: 22px; color: var(--text-light);
    font-size: 13px; line-height: 18px;
  }

  .card-back { background: var(--card-black); }
  .back-pattern {
    position: absolute; inset: 0;
    background: linear-gradient(135deg, #0f0f0f 0%, #1f1f1f 45%, #121212 100%);
  }
  .back-brand {
    left: 50%; top: 50%; transform: translate(-50%, -50%);
    color: var(--text-light); font-size: 18px; white-space: nowrap;
  }
  .back-brand .brand-mark { border: 2px solid var(--text-light); }
</style>
</head>
<body>
<main class="stage">
  <section class="card card-front">
    <svg class="front-shapes" viewBox="0 0 540 309" width="540" height="309" aria-hidden="true">
      <defs>
        <linearGradient id="darkPanel" x1="0" y1="0" x2="1" y2="1">
          <stop offset="0" stop-color="#3a3a3a"/>
          <stop offset="0.45" stop-color="#161616"/>
          <stop offset="1" stop-color="#0e0e0e"/>
        </linearGradient>
      </defs>
      <path d="M272,0 C232,90 230,195 60,238 L0,250 L0,309 L540,309 L540,0 Z" fill="var(--silver-light)"/>
      <path d="M286,0 C246,92 240,200 70,246 L0,258 L0,309 L540,309 L540,0 Z" fill="var(--silver)"/>
      <path d="M300,0 C262,95 250,210 80,256 L0,268 L0,309 L540,309 L540,0 Z" fill="url(#darkPanel)"/>
    </svg>

    <div class="brand front-brand">
      <span class="brand-mark"></span>
      <span>Cedar Ridge Mechanical</span>
    </div>

    <div class="holder">
      <p class="holder-name">DANIEL REYES</p>
      <p class="holder-role">Manager</p>
    </div>

    <ul class="contact-list">
      <li>123-456-2100
        <span class="contact-icon"><svg width="8" height="8" viewBox="0 0 10 10" aria-hidden="true"><path d="M2,1 L4,1 L4.6,3 L3.5,4 C4,5.3 4.8,6 6,6.5 L7,5.4 L9,6 L9,8 C5,8.5 1.5,5 2,1 Z" fill="#141414"/></svg></span>
      </li>
      <li>youremail@mailbox.com
        <span class="contact-icon"><svg width="8" height="8" viewBox="0 0 10 10" aria-hidden="true"><rect x="1" y="2.5" width="8" height="5.5" fill="none" stroke="#141414" stroke-width="1.2"/><path d="M1,2.5 L5,5.5 L9,2.5" fill="none" stroke="#141414" stroke-width="1.2"/></svg></span>
      </li>
      <li>www.yourwebsite.com
        <span class="contact-icon"><svg width="8" height="8" viewBox="0 0 10 10" aria-hidden="true"><circle cx="5" cy="5" r="3.8" fill="none" stroke="#141414" stroke-width="1.1"/><path d="M1.2,5 H8.8 M5,1.2 C3,3.5 3,6.5 5,8.8 M5,1.2 C7,3.5 7,6.5 5,8.8" fill="none" stroke="#141414" stroke-width="0.9"/></svg></span>
      </li>
    </ul>

    <p class="address">Your address, city<br>state, ZIP 0000</p>
  </section>

  <section class="card card-back">
    <div class="back-pattern" role="img" aria-label="Repeating glossy pattern of the company mark across the card back"></div>
    <div class="brand back-brand">
      <span class="brand-mark"></span>
      <span>Cedar Ridge Mechanical</span>
    </div>
  </section>
</main>
</body>
</html>
```